Dental Practice Billboard Design

We are a newer dental practice in need of a simple but appealing billboard for our growing dental practice to attract new patients. The practice is owned by husband and wife dentists and is family friendly in a small town in Kentucky. We try to be very friendly and caring to our patients. Would prefer a blue background for the billboard and our tooth logo to be prominent. We are partial to the Patua One font used in the image below but please feel free to tweak it as you deem necessary. The shape of the uppercase D and lowercase g are why we like that font, so fonts with a similarly shaped “D” and “g” would work as well. Please include our phone number (555) 847-1390. Please see our website Harlowbrookdentistry.example for more info on the practice if needed. Thank you! Looking forward to seeing your creation.
Updates

The dimensions will be 12ft x 24ft (3.6576m x 7.3152m). Apologies for not including this in the original prompt. Thank you all for your submissions.

Industry/Entity Type

Dental

Font styles to use
Other font styles liked:
• Patua One

Colors
0054AA
0677BA
7BADD7
CADEEF
E8F1F8
0094D4
00A9DD
6FCCEA
C7EBF8
E9F6FB
00AB8E
00BBA5
67D7C9
C6EFE9
E9F9F6
59FF00
82FF00
B8FF75
E3FFCB
F4FFEA

Requirements
Must have
• Phone number, website, Logo, Practice name “Harlow Brook Dentistry”
Should not have
• A tagline or slogan

```html
<!DOCTYPE html>
<html lang="en">
<head>
<meta charset="utf-8">
<title>Harlow Brook Dentistry Billboard</title>
<link rel="stylesheet" href="https://fonts.googleapis.com/css2?family=Patua+One&display=swap">
<style>
  :root {
    --stage: #808080;
    --board-blue: #0054b9;
    --brand-green: #14b214;
    --white: #ffffff;
  }
  * { margin: 0; padding: 0; box-sizing: border-box; }
  html, body { width: 1200px; height: 1059px; overflow: hidden; }
  body { background: var(--stage); font-family: "Patua One", serif; position: relative; }

  .billboard {
    position: absolute; left: 208px; top: 332px;
    width: 784px; height: 392px;
    background: var(--board-blue); overflow: hidden;
  }
  .practice-name { position: absolute; left: 32px; top: 26px; }
  .practice-name__lead {
    display: block; color: var(--brand-green);
    font-size: 62px; line-height: 1; letter-spacing: -0.5px;
  }
  .practice-name__sub {
    display: block; color: var(--white);
    font-size: 50px; line-height: 1; margin-top: 14px;
  }

  .contact-row {
    position: absolute; left: 32px; display: flex; align-items: center;
    color: var(--white);
  }
  .contact-row--phone { top: 222px; font-size: 40px; }
  .contact-row--web { top: 280px; font-size: 22px; letter-spacing: 1.2px; }
  .contact-row__icon { flex: none; margin-right: 9px; }

  .hours-band {
    position: absolute; left: 0; top: 338px; width: 540px; height: 54px;
    background: var(--brand-green); display: flex; align-items: center;
    padding-left: 32px;
  }
  .hours-band__label { color: var(--board-blue); font-size: 18px; letter-spacing: 1px; margin-right: 10px; }
  .hours-band__list { color: var(--white); font-size: 15px; letter-spacing: 1px; line-height: 1.35; }

  .brand-mark {
    position: absolute; left: 440px; top: 0; width: 344px; height: 392px;
    display: flex; flex-direction: column; align-items: center; justify-content: center;
  }
  .brand-mark__dot {
    width: 110px; height: 110px; border-radius: 50%;
    background: var(--brand-green); margin-bottom: 22px;
  }
  .brand-mark__name {
    color: var(--white); font-size: 40px; line-height: 1.05; text-align: center;
  }
</style>
</head>
<body>
  <main class="billboard">
    <h1 class="practice-name">
      <span class="practice-name__lead">Harlow Brook</span>
      <span class="practice-name__sub">Dentistry</span>
    </h1>

    <p class="contact-row contact-row--phone">
      <svg class="contact-row__icon" width="31" height="31" viewBox="0 0 24 24" aria-hidden="true">
        <path fill="#14b214" d="M6.6 10.8a15.1 15.1 0 0 0 6.6 6.6l2.2-2.2c.3-.3.7-.4 1-.2 1.1.4 2.3.6 3.6.6.6 0 1 .4 1 1V20c0 .6-.4 1-1 1A17 17 0 0 1 3 4c0-.6.4-1 1-1h3.5c.6 0 1 .4 1 1 0 1.3.2 2.5.6 3.6.1.3 0 .7-.2 1z"/>
        <path fill="none" stroke="#14b214" stroke-width="1.8" stroke-linecap="round" d="M14 2.5a7.5 7.5 0 0 1 7.5 7.5M14 6a4 4 0 0 1 4 4"/>
      </svg>
      (555) 847-1390
    </p>

    <p class="contact-row contact-row--web">
      <svg class="contact-row__icon" width="27" height="27" viewBox="0 0 24 24" aria-hidden="true">
        <g fill="none" stroke="#14b214" stroke-width="1.8">
          <circle cx="12" cy="12" r="10"/>
          <ellipse cx="12" cy="12" rx="4.5" ry="10"/>
          <path d="M2 12h20M3.5 7h17M3.5 17h17"/>
        </g>
      </svg>
      Harlowbrookdentistry.example
    </p>

    <div class="hours-band">
      <span class="hours-band__label">OFFICE HOURS:-</span>
      <div class="hours-band__list">
        <div>Mon - Tue - Thu - Fri : 8AM - 5PM</div>
        <div>Sat - Sun - Wed : CLOSED</div>
      </div>
    </div>

    <div class="brand-mark">
      <div class="brand-mark__dot"></div>
      <p class="brand-mark__name">Harlow Brook<br>Dentistry</p>
    </div>
  </main>
</body>
</html>
```